Tralha Cesto Website

Tralha Cesto is a brazilian Self Storage in a Box where customers can store all the clutter that they have out of their houses. We deliver one or more boxes at their homes, they fill the boxes with their stuff and we store it for them.

"Tralha" means something like "mess" in portuguese. So the name would means something like "Mess Box" or "Clutter Box".

How it works:
1) The customer asks for 1 or more boxes.
2) Tralha Cesto leaves the boxes at their houses
3) The clients fill the boxes with their stuff
4) Customers call Tralha Cesto for the pick up
5) We get the boxes and store them
6) When the customer wants the box back they can order it online or by phone and wait for the box delivery.
-

We have already produced a flyer to launch the service. You can see this flyer at "Project Files".

We want the website to have a startup "look and fell". Here are some websites of similar services that we like very much.
- www.crateowl.example
- www.stowpod.example

We are planning this launching website to have only 2 pages. The Landing Page and a FAQ page. We are producing an explainer video. The proposed designs must think about a special place to place the video.

We are still writing it´s content but you can use the flyer as a reference.

Thanks.
Updates

Project Deadline Extended
Reason: The project was refundable but as we have already received good design options, now we are turning it to Non Refundable and giving more time for new designers to send their proposals. Thanks.

Project Deadline Extended

Target Market(s)

Young couples having kids
Students
Families in need of more space at home

Industry/Entity Type

Store

Requirements
Must have
• Special place to place the explainer video (still being produced).

How it works drawing. You can use the one on the flyer or draw a new one (recomended).

Transparent box drawings (showing it´s content). I will serve to show the clients what they can store with the service.

Clutter Room Before/After Pic/drawings (showing how the service can benefit the client).

```html
<!DOCTYPE html>
<html lang="pt">
<head>
<meta charset="utf-8">
<title>Tralha Cesto</title>
<link href="https://fonts.googleapis.com/css2?family=Open+Sans:ital,wght@0,400;0,600;0,700;1,600&display=swap" rel="stylesheet">
<style>
:root{
  --blue:#1466b4;
  --blue-dark:#0c549c;
  --orange:#f7941d;
  --orange-deep:#ef7d0a;
  --ink:#333;
  --muted:#555;
  --grey-bg:#eeeeee;
  --footer:#3b3d42;
  --footer-dark:#2b2d31;
}
*{box-sizing:border-box;margin:0;padding:0}
html,body{width:746px;height:1200px;overflow:hidden}
body{font-family:"Open Sans",sans-serif;color:var(--ink);background:#fff;position:relative}
.abs{position:absolute}
/* header */
.header{top:0;left:0;width:746px;height:82px;background:#fff}
.logo{left:135px;top:52px;display:flex;align-items:center;gap:6px;font-size:16px;font-weight:700;color:var(--blue);white-space:nowrap}
.logo .mark{width:12px;height:12px;background:var(--orange);border-radius:50%}
.toplinks{left:427px;top:30px;font-size:7px;color:#777;white-space:nowrap}
.phone{left:518px;top:24px;font-size:15px;font-weight:600;color:var(--blue);white-space:nowrap}
.nav{left:377px;top:53px;display:flex;gap:17px;font-size:9.5px;color:#444;white-space:nowrap}
.nav .active{border-bottom:2px solid var(--orange);padding:0 4px 2px}
/* hero */
.hero{top:82px;left:0;width:746px;height:222px;background:linear-gradient(180deg,#1770c2,#0d5aa6)}
.video{left:137px;top:113px;width:268px;height:165px;background:radial-gradient(circle at 50% 45%,#ff9a1a,#f07c00);border:2px solid #e56f00}
.video .w1{position:absolute;top:50px;width:100%;text-align:center;color:#fff;font-weight:600;font-size:18px}
.video .w2{position:absolute;top:70px;width:100%;text-align:center;color:#fff;font-weight:700;font-size:25px}
.video .bar{position:absolute;left:2px;right:2px;bottom:2px;height:12px;background:#8a4a05;display:flex;align-items:center}
.video .play{width:18px;height:10px;background:#222;margin-left:2px}
.video .track{flex:1;height:3px;background:#c06a0a;margin:0 6px}
.video .side{position:absolute;right:3px;top:3px;width:12px;display:flex;flex-direction:column;gap:2px}
.video .side span{height:10px;background:#3a2a1a}
.hero-title{left:433px;top:120px;color:#fff;font-size:21px;line-height:1.2;font-weight:700;white-space:nowrap}
.hero-text{left:433px;top:180px;width:200px;color:#e4eefa;font-size:7px;line-height:15px}
.start{left:438px;top:245px;width:84px;height:28px;background:#f4f4f4;border:1px solid #ddd;color:#555;font-size:12px;display:flex;align-items:center;justify-content:center}
.ok{left:513px;top:240px;width:14px;height:14px;border-radius:50%;background:var(--orange);color:#fff;font-size:6px;display:flex;align-items:center;justify-content:center}
/* how */
.how-title{left:147px;top:338px;font-size:20px;font-weight:400;color:#222}
.how-rule{left:137px;top:365px;width:236px;height:1px;background:#ccc}
.steps{left:145px;top:386px;list-style:none;font-size:8px;color:#333;white-space:nowrap}
.steps li{height:20px;padding-left:20px;position:relative}
.steps li.arrow::before{content:"";position:absolute;left:0;top:1px;border-left:9px solid var(--orange);border-top:4px solid transparent;border-bottom:4px solid transparent}
.feat{width:100px;text-align:center;font-size:5.5px;color:#444;line-height:7.5px}
.feat .c{width:64px;height:64px;border-radius:50%;background:var(--orange);margin:0 auto 6px;border:2px solid #f9b04d}
.feat .u{width:40px;height:1px;background:var(--orange);margin:3px auto 0}
/* safety */
.safety{top:563px;left:0;width:746px;height:205px;background:var(--grey-bg)}
.notch{left:372px;top:563px;border-top:7px solid var(--blue);border-left:8px solid transparent;border-right:8px solid transparent}
.safety-title{left:0;width:764px;top:582px;text-align:center;font-size:17px;font-weight:600;color:#444}
.s-rule{left:325px;top:605px;width:113px;height:2px;background:var(--blue)}
.pillar{width:160px;text-align:center}
.pillar .ico{width:36px;height:36px;margin:0 auto;border:1px solid #aaa;border-radius:4px;background:#fafafa;display:flex;align-items:center;justify-content:center}
.pillar h3{margin-top:20px;font-size:8.5px;font-weight:600;color:#333}
.pillar p{margin-top:5px;font-size:6.5px;color:#444;line-height:11px}
/* press */
.press{top:768px;left:0;width:746px;height:28px;background:var(--orange);display:flex;align-items:center;justify-content:center;gap:22px;color:#5a3600;font-size:9px;font-weight:600}
/* pricing */
.product{background:linear-gradient(180deg,#c8c8c8,#8a8a8a)}
.price{width:150px}
.price h4{font-size:12px;font-weight:400;color:#333}
.price .amt{font-size:10.5px;color:var(--orange-deep);margin-top:2px}
.price ul{list-style:none;margin-top:6px;font-size:5.2px;color:#444;line-height:6px}
.price li{padding-left:9px;position:relative;margin-bottom:4px}
.price li::before{content:"";position:absolute;left:0;top:1px;width:3px;height:3px;background:var(--orange)}
.cta{left:311px;top:935px;width:124px;height:22px;background:linear-gradient(#444,#1a1a1a);color:#fff;font-size:11px;display:flex;align-items:center;justify-content:center;border-radius:2px}
/* before after */
.ba{top:973px;left:0;width:746px;height:118px;background:#f0f0f0;border-top:1px solid #ddd}
.ba-title{left:143px;top:1008px;font-size:15.5px;font-style:italic;font-weight:600;color:#666;line-height:23px;text-align:center}
.photo{top:989px;width:147px;height:83px}
.tag{width:40px;height:14px;background:var(--orange);color:#fff;font-size:7px;font-style:italic;display:flex;align-items:center;justify-content:center}
/* footer */
.footer{top:1091px;left:0;width:746px;height:84px;background:var(--footer)}
.flinks{left:142px;font-size:7px;color:#ddd;white-space:nowrap}
.social{top:1152px;width:14px;height:14px;border-radius:50%;background:#888}
.contact{left:431px;font-size:7px;color:#ddd;display:flex;align-items:center;gap:7px;white-space:nowrap}
.bottom{top:1175px;left:0;width:746px;height:25px;background:var(--footer-dark);font-size:5.5px;color:#ddd}
</style>
</head>
<body>
<header class="abs header">
  <div class="abs logo"><span class="mark"></span>Tralha Cesto</div>
  <div class="abs toplinks">Login / Faq's / Contact</div>
  <div class="abs phone">(21) 4000-1234</div>
  <nav class="abs nav"><span class="active">Home</span><span>About</span><span>How it works</span><span>Pricing</span><span>Security</span></nav>
</header>

<section class="abs hero"></section>
<div class="abs video" role="img" aria-label="Explainer video player">
  <div class="w1">Welcome</div>
  <div class="w2">Tralha cesto</div>
  <div class="side"><span></span><span></span><span></span></div>
  <div class="bar"><span class="play"></span><span class="track"></span></div>
</div>
<h1 class="abs hero-title">Reconquiste of<br>espaco da sua casa</h1>
<p class="abs hero-text">luctus at sit amet urna. Quisque non augue tincidunt, egest as massa non, elementum sem. Suspendisse mollis nulla eu lorem ultricies dapibus.</p>
<div class="abs start">Start Now</div>
<div class="abs ok">ok</div>

<h2 class="abs how-title">How it Works</h2>
<div class="abs how-rule"></div>
<ul class="abs steps">
  <li class="arrow">The customer asks for 1 or more boxes.</li>
  <li class="arrow">Tralha Cesto leaves the boxes at their houses</li>
  <li class="arrow">The clients fill the boxes with their stuff</li>
  <li class="arrow">Customers call Tralha Cesto for the pick up</li>
  <li class="arrow">We get the boxes and store them</li>
  <li class="arrow">When the customer wants the box back they can</li>
  <li>order it online or by phone and wait for the box delivery</li>
</ul>
<div class="abs feat" style="left:404px;top:342px"><div class="c" role="img" aria-label="Illustration of home pick up"></div>CONVENIENT PICK UP<br>OF YOUR ITEMS<div class="u"></div></div>
<div class="abs feat" style="left:514px;top:342px"><div class="c" role="img" aria-label="Illustration of filling a box"></div>YOU FILL THEM, AND<br>SCHEDULE A PICKUP<div class="u"></div></div>
<div class="abs feat" style="left:404px;top:446px"><div class="c" role="img" aria-label="Illustration of delivery truck"></div>ON DEMAND RETURN<br>OF STORED ITEMS<div class="u"></div></div>
<div class="abs feat" style="left:514px;top:446px"><div class="c" role="img" aria-label="Illustration of secure storage"></div>YOUR BOXES ARE<br>SECURED IN STORAGE.<div class="u"></div></div>

<section class="abs safety"></section>
<div class="abs notch"></div>
<h2 class="abs safety-title">SAFETY &amp; SECURITY</h2>
<div class="abs s-rule"></div>
<div class="abs pillar" style="left:135px;top:636px">
  <div class="ico"><svg width="22" height="22" viewBox="0 0 22 22"><circle cx="11" cy="11" r="9" fill="none" stroke="#666" stroke-width="2"/><rect x="7" y="9" width="8" height="5" fill="#666"/></svg></div>
  <h3>SEGURANCA</h3>
  <p>tenha sua colsas armazenadas em um<br>amblente seguro, monitorado 24 horas por dia</p>
</div>
<div class="abs pillar" style="left:304px;top:636px">
  <div class="ico"><svg width="22" height="22" viewBox="0 0 22 22"><circle cx="11" cy="11" r="9" fill="none" stroke="#666" stroke-width="2"/><path d="M6 11l4 4 7-8" fill="none" stroke="#666" stroke-width="2.5"/></svg></div>
  <h3>PRATICIDADE</h3>
  <p>escoha orcebimento de suas cosas em<br>sua casa ou emum de nossos pontos de coleta<br>no flamongo, tijuca, Ilha do governador<br>e recrelo do bandelrantes</p>
</div>
<div class="abs pillar" style="left:464px;top:636px">
  <div class="ico"><svg width="22" height="22" viewBox="0 0 22 22"><circle cx="11" cy="11" r="9" fill="none" stroke="#666" stroke-width="2"/><path d="M5 12l4-3 4 3 4-3" fill="none" stroke="#666" stroke-width="2.5"/></svg></div>
  <h3>ECONOMLA</h3>
  <p>apovelte melhoro espco que voce ja tem<br>dentro de casa</p>
</div>

<div class="abs press"><span>Metro Ledger</span><span>Capital Weekly</span><span>Channel Nine</span><span>Market Wire</span><span>Startup Daily</span><span>Coast Herald</span></div>

<div class="abs product" style="left:150px;top:842px;width:78px;height:66px" role="img" aria-label="Large storage container"></div>
<div class="abs price" style="left:255px;top:826px">
  <h4>A PARTIR DE</h4><div class="amt">R$69,00 / mes</div>
  <ul><li>Diraensoes largura x xomprinentox<br>altra volume total : 800 litros</li><li>Valor armazenagen</li><li>Valor anterga nos pontos de coleta</li><li>Volor entrega em domicilo</li></ul>
</div>
<div class="abs product" style="left:405px;top:852px;width:80px;height:54px;border-radius:4px" role="img" aria-label="Storage crate"></div>
<div class="abs price" style="left:509px;top:826px">
  <h4>A PARTIR DE</h4><div class="amt">R$14,90 / mes</div>
  <ul><li>Diraensoes largura x xomprinentox<br>altra volume total : 800 litros</li><li>Valor armazenagen</li><li>Valor anterga nos pontos de coleta</li><li>Volor entrega em domicilo</li></ul>
</div>
<div class="abs cta">Now started</div>

<section class="abs ba"></section>
<div class="abs ba-title">CLUTTER ROOM<br>&nbsp;&nbsp;&nbsp;Before/After</div>
<svg class="abs" style="left:270px;top:1018px" width="20" height="26"><path d="M4 2l12 11-12 11" fill="none" stroke="#ddd" stroke-width="5"/></svg>
<div class="abs photo" style="left:301px;background:linear-gradient(135deg,#6a6f78,#3c3f47)" role="img" aria-label="Cluttered room before"><div class="tag">Before</div></div>
<div class="abs photo" style="left:458px;background:linear-gradient(135deg,#c9a56a,#6b5a44)" role="img" aria-label="Tidy room after"><div class="tag">After</div></div>

<footer class="abs footer"></footer>
<div class="abs flinks" style="top:1115px">Home &nbsp;| &nbsp;About &nbsp;| &nbsp;How it works &nbsp;| &nbsp;Pricing &nbsp;| &nbsp;Security</div>
<div class="abs flinks" style="top:1130px">Contact us &nbsp;&nbsp;| &nbsp;faq's &nbsp;| &nbsp;News &nbsp;| &nbsp;login</div>
<div class="abs social" style="left:144px"></div><div class="abs social" style="left:160px"></div><div class="abs social" style="left:176px"></div>
<div class="abs contact" style="top:1111px"><svg width="9" height="11"><path d="M4.5 0a4 4 0 0 1 4 4c0 3-4 7-4 7s-4-4-4-7a4 4 0 0 1 4-4z" fill="#ddd"/><circle cx="4.5" cy="4" r="1.5" fill="#3b3d42"/></svg>venenatis neque sit amet ante aliquam sollicitudin</div>
<div class="abs contact" style="top:1129px"><svg width="9" height="10"><path d="M1 1l3 0 1 3-2 1a6 6 0 0 0 3 3l1-2 3 1v3C4 10 0 6 1 1z" fill="#ddd"/></svg>0800-555-0101 &nbsp;/ &nbsp;0800-555-0199</div>
<div class="abs contact" style="top:1147px"><svg width="10" height="8"><rect width="10" height="8" fill="#ddd"/><path d="M0 0l5 4 5-4" fill="none" stroke="#3b3d42"/></svg>contato@tralhacesto.example</div>
<div class="abs" style="left:360px;top:1163px;border-bottom:12px solid var(--footer-dark);border-left:7px solid transparent;border-right:7px solid transparent"></div>
<div class="abs bottom"><span class="abs" style="left:133px;top:8px">copyrights © 2014 tralhacesto.example</span><span class="abs" style="left:569px;top:8px">All rights reserved</span></div>
</body>
</html>
```